Events Company Needs Website Revamp

Tallwood Expos is an events company that specializes in organizing and marketing large scale consumer and trade events globally.

The new web design should provide easy classification of the events, and allow visitors to find and access the details page within 2 clicks.

There are no strict guidelines on the color theme. It just has to blend naturally with the corporate logo.
Updates

The company logo is uploaded (pdf & ai)

I came across this design which I like very much. Elegant and corporate with nice modern fonttype.

Layout wise, neat and clear. 

Please see how you can emulate the design further. Particularly, highlighting the 2 event arms (Trade/Consumer) clearly.

Target Market(s)

Consumer looking for upcoming events, B2C companies looking to participate, B2B companies looking to connect with other companies

Industry/Entity Type

It Company

Requirements
Must have
• The new design should help to achieve the following objectives:
1) Visitors should be able to easily identify and access the 2 different types of events (i.e. Trade Events and Consumer Events).
2) Visitors should be able to easily find events that interest them (e.g. filter by date, trade or consumer, category [i.e. beauty, retail, F&B, construction, etc.]).
3) Visitors should be able to access an event’s details page within 2 clicks from any page.

Main navigation to include the following links:
- About Us
- Calendar
- Consumer Events
- Trade Events
- Contact Us

Design for Three (3) pages required:
A. Homepage
- Clear differentiation and easy access to the 2 different types of events (trade and consumer)
- Featured area to showcase latest 4-5 events
- Quick way to access events calendar
- Clear call-to-action for newsletter signup
- Social media sharing widgets/buttons
- A section for latest news and press releases
- A section for featured testimonials

B. Events Listing Page
- List of links to all events
- Logos and/or photos of events
- Filter / tags to find events in a specific category (e.g. food, electronics, building & construction, etc.)

C. Events Details Page
- Photo strip to showcase event photos / brochure
- A section with event details (Date, Venue, Event Description, etc.)
- Call-to-action button to visit event website
- Call-to-action button to contact event sales team
- E.g. http://vantly-demo.com/user/brightfoxhk/brightfox-monday-2011 but with the photo strip permanently extended and of a shorter height. Event details and call-to-action buttons should also be easily seen

```html
<!DOCTYPE html>
<html lang="en">
<head>
<meta charset="utf-8">
<title>Tallwood Expos</title>
<link href="https://fonts.googleapis.com/css2?family=Oswald:wght@400;500&family=Poiret+One&family=PT+Sans:ital,wght@0,400;0,700;1,400&display=swap" rel="stylesheet">
<style>
:root{
  --purple-dark:#440a43;
  --purple:#6d106b;
  --purple-deep:#3a0838;
  --orange:#f08a24;
  --ink:#222;
  --grey-text:#888;
  --link:#6a1a68;
  --cal-cell:#edf4fc;
  --cal-line:#d6dde6;
  --hatch:#e4e4e4;
}
*{margin:0;padding:0;box-sizing:border-box}
html,body{width:969px;height:1200px;overflow:hidden;background:#fff}
body{position:relative;font-family:"PT Sans",sans-serif;color:var(--ink)}
.abs{position:absolute}

/* header */
.site-header{position:absolute;left:0;top:0;width:969px;height:160px}
.header-band{position:absolute;left:0;top:0;width:969px;height:146px;background:linear-gradient(180deg,var(--purple-dark) 0%,#5e0d5c 55%,var(--purple) 100%)}
.header-curve{position:absolute;left:0;top:140px}
.brand{position:absolute;left:45px;top:-75px;width:160px;height:160px;border-radius:50%;background:#fff;border:4px solid #8a1d88;display:flex;align-items:flex-end;justify-content:center;padding-bottom:40px}
.brand-name{font-family:"PT Sans",sans-serif;font-size:15px;color:#444;font-weight:400;display:flex;align-items:center;gap:6px}
.brand-name .dot{width:10px;height:10px;border-radius:50%;background:var(--orange)}
.main-nav{position:absolute;left:342px;top:0;width:627px;height:93px;background:rgba(40,4,40,.28)}
.main-nav .item{position:absolute;top:0;height:57px;display:flex;align-items:center;justify-content:center;font-family:"Oswald",sans-serif;font-size:21px;color:#fff;border-right:1px solid rgba(255,255,255,.12)}
.sub-nav{position:absolute;top:66px;left:16px;display:flex}
.sub-nav span{width:100px;text-align:center;font-size:12.5px;color:#fff;border-right:1px solid rgba(255,255,255,.2);line-height:16px}

/* arms */
.arm-title{position:absolute;top:228px;font-family:"Poiret One",sans-serif;font-size:42px;color:#111;font-weight:400}
.arm-text{position:absolute;top:301px;width:265px;font-size:14px;line-height:21px;color:var(--grey-text)}
.btn-more{position:absolute;top:385px;width:96px;height:33px;background:linear-gradient(#fff,#e2e2e2);border:1px solid #c9c9c9;font-family:"Oswald",sans-serif;font-size:14px;color:#555;display:flex;align-items:center;justify-content:center}
.hatch{position:absolute;height:9px;background:repeating-linear-gradient(135deg,var(--hatch) 0 2px,#fff 2px 5px)}
.globe{position:absolute;left:348px;top:175px;width:294px;height:290px;border-radius:50%;background:radial-gradient(circle at 40% 35%,#fafafa,#d6d6d6 60%,#aaa 100%)}

/* featured */
.featured{position:absolute;left:43px;top:498px;width:886px;height:62px}
.featured-label{position:absolute;left:0;top:0;width:147px;height:62px;background:linear-gradient(#f3f3f3,#cfcfcf);font-family:"Poiret One",sans-serif;font-size:14px;font-weight:700;display:flex;align-items:center;padding-left:15px;color:#333}
.featured-arrow{position:absolute;top:0;width:27px;height:62px;background:linear-gradient(#f3f3f3,#d2d2d2);border-left:1px solid #bbb;display:flex;align-items:center;justify-content:center}
.photo{position:absolute;top:0;width:96px;height:61px}

/* columns */
.col-title{position:absolute;top:649px;font-family:"Poiret One",sans-serif;font-size:29px;color:#111}
.news-thumb{position:absolute;left:44px;width:47px;height:47px;border:1px solid #ddd;background:#fff;padding:5px}
.news-thumb div{width:100%;height:100%;background:linear-gradient(#f7b84a,#5aa3c9)}
.news-title{position:absolute;left:103px;font-family:"Oswald",sans-serif;font-size:15px;color:#666;width:221px;padding-bottom:4px;background:repeating-linear-gradient(135deg,var(--hatch) 0 2px,#fff 2px 5px) bottom/100% 5px no-repeat}
.body-text{position:absolute;font-size:14px;line-height:20px;color:var(--grey-text)}
.read-more{position:absolute;font-size:14px;color:var(--link)}
.quote-mark{position:absolute;left:368px;font-family:"Oswald",sans-serif;font-size:44px;color:#999;line-height:1}
.quote-by{position:absolute;left:400px;width:232px;text-align:right;font-size:13.5px;font-style:italic;color:#111}

/* calendar */
.calendar{position:absolute;left:664px;top:656px;width:266px;height:268px;background:var(--cal-cell)}
.cal-head{height:32px;background:#0d0b0d;display:flex;align-items:center;padding-left:17px;color:#fff;font-size:13px}
.cal-select{margin-left:27px;width:187px;height:16px;background:#fff;color:#000;font-size:12px;padding-left:4px;position:relative;line-height:16px}
.cal-select i{position:absolute;right:0;top:0;width:22px;height:16px;background:var(--purple-dark)}
.cal-select i:after{content:"";position:absolute;left:6px;top:5px;border:5px solid transparent;border-top:6px solid #fff;border-bottom:0}
.cal-grid{display:grid;grid-template-columns:repeat(3,1fr);grid-template-rows:repeat(4,59px)}
.month{border-right:1px solid var(--cal-line);border-bottom:1px solid var(--cal-line);padding:6px 0 0 11px;font-family:"Oswald",sans-serif;font-size:20px;color:#6d7a86;position:relative}
.month:nth-child(3n){border-right:0}
.month .marks{display:flex;gap:4px;margin-top:2px}
.month .marks b{width:10px;height:7px;background:#6d7a86;border-radius:3px 3px 1px 1px}
.tooltip{position:absolute;left:766px;top:804px;width:159px;height:25px;background:var(--purple-deep);color:#fff;font-size:12px;display:flex;align-items:center;justify-content:center}
.tooltip:before{content:"";position:absolute;left:18px;top:-6px;border:6px solid transparent;border-bottom-color:var(--purple-deep);border-top:0}

/* footer */
.footer-line{position:absolute;left:0;top:998px}
.foot-h{position:absolute;top:1059px;font-family:"Oswald",sans-serif;font-size:14px;color:#111;font-weight:500}
.foot-t{position:absolute;font-size:13px;color:#666;line-height:15px}
.social{position:absolute;top:1084px;left:432px;display:flex;gap:9px}
.social span{width:27px;height:27px;border-radius:50%;background:var(--purple-deep)}
.subscribe{position:absolute;left:613px;top:1102px;display:flex}
.subscribe .field{width:169px;height:21px;border:1px solid #ccc;font-size:12px;font-style:italic;color:#888;padding:3px 7px}
.subscribe .go{width:52px;height:21px;background:linear-gradient(#fff,#e0e0e0);border:1px solid #ccc;border-left:0;font-size:10px;font-weight:700;color:var(--purple-deep);display:flex;align-items:center;justify-content:center}
.to-top{position:absolute;left:886px;top:1108px;text-align:center;font-size:12px;width:30px}
</style>
</head>
<body>

<header class="site-header">
  <div class="header-band"></div>
  <svg class="header-curve" width="969" height="20" viewBox="0 0 969 20">
    <rect x="0" y="5" width="969" height="3" fill="#f08a24"/>
    <path d="M0 8 Q484 18 969 8 Z" fill="#440a43"/>
  </svg>
  <div class="brand"><span class="brand-name"><span class="dot"></span>Tallwood Expos</span></div>
  <nav class="main-nav">
    <div class="item" style="left:0;width:101px">About Us</div>
    <div class="item" style="left:101px;width:96px">Calendar</div>
    <div class="item" style="left:197px;width:128px">Trade Events</div>
    <div class="item" style="left:325px;width:163px">Consumer Events</div>
    <div class="item" style="left:488px;width:120px;border-right:0">Contact Us</div>
    <div class="sub-nav"><span>Our &nbsp; Story</span><span>History</span><span>Missios</span></div>
  </nav>
</header>

<main>
  <h2 class="arm-title" style="left:46px">Trade Events</h2>
  <p class="arm-text" style="left:46px">Lorem ipsum dolor sit amet, consectetur adipiscing elit. Curabitur ac lorem eu sem congue pharetra. Vestibulum eget lacus nibh.</p>
  <div class="btn-more" style="left:43px">View More</div>
  <div class="hatch" style="left:43px;top:436px;width:307px"></div>

  <div class="globe" role="img" aria-label="Sphere made of white cubes carrying event logos"></div>

  <h2 class="arm-title" style="left:638px">Consumer Events</h2>
  <p class="arm-text" style="left:668px;text-align:right">Lorem ipsum dolor sit amet, consectetur adipiscing elit. Curabitur ac lorem eu sem congue pharetra. Vestibulum eget lacus nibh.</p>
  <div class="btn-more" style="left:837px">View More</div>
  <div class="hatch" style="left:625px;top:436px;width:307px"></div>

  <section class="featured">
    <div class="featured-label">Featured Events</div>
    <div class="featured-arrow" style="left:148px"><svg width="12" height="24"><path d="M12 0 L0 12 L12 24Z" fill="#5a0e58"/></svg></div>
    <div class="featured-arrow" style="left:176px"><svg width="12" height="24"><path d="M0 0 L12 12 L0 24Z" fill="#5a0e58"/></svg></div>
    <div class="photo" role="img" aria-label="Speaker on stage at a conference" style="left:204px;background:linear-gradient(#3a2a22,#8a6a52)"></div>
    <div class="photo" role="img" aria-label="Hand on a computer mouse" style="left:301px;background:linear-gradient(#7a3f7a,#d9c8d6)"></div>
    <div class="photo" role="img" aria-label="Business handshake at a meeting" style="left:398px;background:linear-gradient(#d9d9dc,#6b5a55)"></div>
    <div class="photo" role="img" aria-label="Team hands joined in a circle" style="left:495px;background:linear-gradient(#6b4a30,#2a1d14)"></div>
    <div class="photo" role="img" aria-label="Seminar audience in a hall" style="left:592px;background:linear-gradient(#d8d6d2,#9a3b35)"></div>
    <div class="photo" role="img" aria-label="Presenter pointing at a screen" style="left:689px;background:linear-gradient(#4f86b6,#cfb79a)"></div>
    <div class="photo" role="img" aria-label="Laptop and keyboard on a desk" style="left:786px;background:linear-gradient(#dfe3e8,#3c3f44)"></div>
  </section>
  <div class="hatch" style="left:43px;top:604px;width:886px"></div>

  <section>
    <h2 class="col-title" style="left:43px">Latest News</h2>
    <div class="news-thumb" style="top:709px" role="img" aria-label="Event logo thumbnail"><div></div></div>
    <div class="news-title" style="top:706px">Lorem Ipsum</div>
    <p class="body-text" style="left:103px;top:741px;width:225px">Lorem ipsum dolor sit amet, vehicula integer tortor libero, mollis sed...</p>
    <a class="read-more" style="left:104px;top:787px">Read More</a>
    <div class="news-thumb" style="top:828px" role="img" aria-label="Event logo thumbnail"><div></div></div>
    <div class="news-title" style="top:825px">Lorem Ipsum</div>
    <p class="body-text" style="left:103px;top:860px;width:225px">Lorem ipsum dolor sit amet, vehicula integer tortor libero, mollis sed...</p>
    <a class="read-more" style="left:104px;top:906px">Read More</a>
  </section>

  <section>
    <h2 class="col-title" style="left:366px">Testimonials</h2>
    <div class="quote-mark" style="top:700px">&ldquo;</div>
    <p class="body-text" style="left:400px;top:705px;width:235px">Lorem ipsum dolor sit amet, consectetur adipiscing elit. Curabitur ac lorem eu sem congue pharetra.</p>
    <div class="quote-by" style="top:768px">Mark Dalton</div>
    <div class="quote-mark" style="top:799px">&ldquo;</div>
    <p class="body-text" style="left:400px;top:804px;width:235px">Lorem ipsum dolor sit amet, consectetur adipiscing elit. Curabitur ac lorem eu sem congue pharetra.</p>
    <div class="quote-by" style="top:867px">Mark Dalton</div>
    <a class="read-more" style="left:400px;top:906px">Read More</a>
  </section>

  <section class="calendar">
    <div class="cal-head">Year <div class="cal-select">2012<i></i></div></div>
    <div class="cal-grid">
      <div class="month">JAN</div><div class="month">FEB</div><div class="month">MAR</div>
      <div class="month">APR<div class="marks"><b></b></div></div>
      <div class="month">MAY<div class="marks"><b></b><b></b><b></b></div></div>
      <div class="month">JUN</div>
      <div class="month">JUL</div><div class="month">AUG</div><div class="month">SEP</div>
      <div class="month">OCT</div><div class="month">NOV</div>
      <div class="month">DEC<div class="marks"><b></b></div></div>
    </div>
  </section>
  <div class="tooltip">Little Steps Fair 2012</div>
</main>

<footer>
  <svg class="footer-line" width="969" height="14" viewBox="0 0 969 14">
    <rect x="0" y="8" width="969" height="3" fill="#f08a24"/>
    <path d="M0 8 Q484 -2 969 8 Z" fill="#440a43"/>
  </svg>
  <div class="foot-h" style="left:45px">Copyright</div>
  <p class="foot-t" style="left:45px;top:1082px">© Tallwood Expos 2009-2010. All Rights Reserved.</p>
  <p class="foot-t" style="left:45px;top:1117px">• Tel: (65) 6200-1180 or (65) 6200-1181<br>• Fax: (65) 6200-1190<br>• hello@tallwoodexpos.example</p>
  <div class="foot-h" style="left:432px">Connect wit Us</div>
  <div class="social"><span></span><span></span><span></span><span></span></div>
  <div class="foot-h" style="left:613px">Subscribe</div>
  <p class="foot-t" style="left:613px;top:1078px;color:#444">Get free event updates &amp; specials!</p>
  <div class="subscribe"><div class="field">Enter Email</div><div class="go">SUBMIT</div></div>
  <div class="to-top">
    <svg width="30" height="46" viewBox="0 0 30 46"><path d="M15 1 L29 17 L21 17 L21 44 L15 38 L9 44 L9 17 L1 17 Z" fill="#f08a24" stroke="#c96a10"/></svg>
    <div>Top</div>
  </div>
</footer>

</body>
</html>
```